Car transport business

We need a new business card design. Attached is our old card sample. I would just like to adjust the logo colors (blue and red) to be brighter. I changed my name to the brighter red and the word dispatcher to a brighter blue as an example. But you can adjust those colors further. And then perhaps you can use the same colors for the card design but use your imagination.

As a suggestion so the card stands out I would like to add a clip art of car carrier truck. Attached are examples of that as well

```html
<!DOCTYPE html>
<html lang="en">
<head>
<meta charset="utf-8">
<title>Crest Haul Business Card</title>
<link rel="stylesheet" href="https://fonts.googleapis.com/css2?family=Open+Sans:wght@400;600;700;800&display=swap">
<style>
  :root {
    --navy: #034a8c;
    --navy-light: #1d5f9c;
    --red: #d8222e;
    --paper: #f3f3f3;
    --stage: #e4e4e4;
    --white: #ffffff;
  }
  * { margin: 0; padding: 0; box-sizing: border-box; }
  html, body { width: 1200px; height: 960px; overflow: hidden; }
  body {
    position: relative;
    background: var(--stage);
    font-family: "Open Sans", Arial, sans-serif;
  }
  .card {
    position: absolute;
    left: 303px;
    width: 592px;
    height: 339px;
    overflow: hidden;
  }
  .card-front { top: 118px; background: var(--navy); }
  .card-back { top: 509px; background: var(--paper); }

  .brand {
    position: absolute;
    z-index: 2;
    display: flex;
    flex-direction: column;
    align-items: flex-start;
  }
  .brand-row { display: flex; align-items: center; gap: 12px; }
  .brand-dot {
    width: 46px; height: 46px; border-radius: 50%;
  }
  .brand-name {
    font-weight: 800;
    font-size: 40px;
    letter-spacing: 9px;
    line-height: 1;
  }
  .brand-tagline {
    margin-left: 58px;
    margin-top: -4px;
    font-weight: 600;
    font-size: 13px;
    letter-spacing: 2.7px;
    text-transform: uppercase;
    white-space: nowrap;
  }

  .card-front .brand { left: 72px; top: 146px; }
  .card-front .brand-dot { background: var(--red); }
  .card-front .brand-name,
  .card-front .brand-tagline { color: var(--white); }

  .carrier-art {
    position: absolute;
    z-index: 1;
    left: 15px; top: 212px;
    width: 562px; height: 125px;
    background: linear-gradient(180deg, var(--navy) 0%, var(--navy-light) 50%, var(--navy) 100%);
  }

  .card-back .brand { left: 92px; top: 86px; }
  .card-back .brand-dot { background: var(--red); }
  .card-back .brand-name,
  .card-back .brand-tagline { color: var(--navy); }

  .holder {
    position: absolute;
    top: 186px; left: 0; width: 100%;
    text-align: center;
  }
  .holder-name {
    color: var(--navy);
    font-weight: 700;
    font-size: 24px;
    line-height: 1.2;
  }
  .holder-role {
    color: var(--red);
    font-weight: 700;
    font-size: 15px;
    letter-spacing: 0.5px;
  }
  .back-waves { position: absolute; left: 0; top: 0; }

  .contacts {
    position: absolute;
    left: 0; top: 306px; width: 100%;
    display: flex; justify-content: center; gap: 16px;
    color: var(--white);
    font-size: 16px;
  }
  .contact { display: flex; align-items: center; gap: 5px; }
  .contact svg { width: 14px; height: 14px; fill: var(--red); }
</style>
</head>
<body>

<section class="card card-front">
  <div class="brand">
    <div class="brand-row">
      <span class="brand-dot"></span>
      <span class="brand-name">CREST HAUL</span>
    </div>
    <span class="brand-tagline">The Auto Transport Professionals</span>
  </div>
  <div class="carrier-art" role="img" aria-label="Faint illustration of a car carrier truck loaded with cars"></div>
</section>

<section class="card card-back">
  <svg class="back-waves" width="592" height="339" viewBox="0 0 592 339">
    <path d="M0,258 Q300,322 592,219 L592,339 L0,339 Z" fill="var(--navy)"/>
    <path d="M0,217 Q210,296 517,253 Q230,302 0,266 Z" fill="var(--red)"/>
  </svg>
  <div class="brand">
    <div class="brand-row">
      <span class="brand-dot"></span>
      <span class="brand-name">CREST HAUL</span>
    </div>
    <span class="brand-tagline">The Auto Transport Professionals</span>
  </div>
  <div class="holder">
    <div class="holder-name">NICO VARGA</div>
    <div class="holder-role">DISPATCHER</div>
  </div>
  <div class="contacts">
    <span class="contact">
      <svg viewBox="0 0 24 24"><path d="M6.6 10.8a15 15 0 0 0 6.6 6.6l2.2-2.2a1 1 0 0 1 1-.25 11.4 11.4 0 0 0 3.6.57 1 1 0 0 1 1 1V20a1 1 0 0 1-1 1A17 17 0 0 1 3 4a1 1 0 0 1 1-1h3.5a1 1 0 0 1 1 1c0 1.25.2 2.45.57 3.6a1 1 0 0 1-.25 1z"/></svg>
      555-014-2286
    </span>
    <span class="contact">
      <svg viewBox="0 0 24 24"><path d="M6 3h12v5H6z M3 9h18v9h-3v3H6v-3H3z M8 15v4h8v-4z"/></svg>
      555-014-7731
    </span>
    <span class="contact">
      <svg viewBox="0 0 24 24"><path d="M2 5h20v14H2z M4 7l8 6 8-6v-0.5H4z" fill-rule="evenodd"/></svg>
      cresthaulinc@mailbox.com
    </span>
  </div>
</section>

</body>
</html>
```